Hi, I need a clean, simple card to hand out to parents for my tutoring business (elementary). I would like the front of the card to have the moose logo below, reading a book. Back should be clean, centered text, no logo just information.

Target Market(s)

Elementary school parents

Industry/Entity Type

Tutoring

Contact Information for Business Card

Front of card:

Moose logo on left + text on right says "Bright Otter Tutoring"

Back of card:

MARA TOLLIVER
email envelope icon + BrightOtterTutoring@quillmail.example

Licensed Harwick Unified Schools Teacher
Delmont Ridge University, M.S. Education

Font styles to use
Serif
Other font styles liked:
• Handwritten font for "Bright Otter Tutoring" and "Mara Tolliver", all else should be serif font

Colors
fee18b
fdf9ce

Requirements
Must have
• Playful, clean, simple. Font listed below.

```html
<!DOCTYPE html>
<html lang="en">
<head>
<meta charset="utf-8">
<title>Bright Otter Tutoring – Business Card</title>
<link rel="stylesheet" href="https://fonts.googleapis.com/css2?family=Caveat:wght@700&family=Noto+Serif:ital,wght@0,400;0,700;1,400&display=swap">
<style>
  :root {
    --page-bg: #ececec;
    --card-mint: #b4f2bd;
    --card-mint-deep: #a3e8ae;
    --brand-red: #7b1d14;
    --ink-green: #2c4a2f;
    --ink-dark: #1f2a20;
    --mark-tan: #c98a4a;
  }
  * { box-sizing: border-box; margin: 0; padding: 0; }
  html, body { width: 1200px; height: 707px; overflow: hidden; }
  body {
    background: var(--page-bg);
    font-family: "Noto Serif", Georgia, serif;
    display: flex;
    align-items: center;
    justify-content: center;
    gap: 60px;
  }
  .card {
    width: 520px;
    height: 297px;
    background: radial-gradient(circle at 55% 45%, var(--card-mint) 0%, var(--card-mint-deep) 100%);
    box-shadow: 0 6px 18px rgba(0,0,0,0.18);
    display: flex;
    flex-direction: column;
    align-items: center;
    justify-content: center;
  }

  /* Front */
  .card-front { gap: 18px; }
  .brand { display: flex; align-items: center; gap: 18px; }
  .brand-mark {
    width: 96px; height: 96px; border-radius: 50%;
    background: var(--mark-tan);
  }
  .brand-name {
    color: var(--brand-red);
    font-size: 34px;
    line-height: 1;
    font-weight: 400;
  }
  .front-email { font-size: 14px; color: var(--ink-dark); }

  /* Back */
  .card-back { text-align: center; gap: 14px; padding: 0 30px; }
  .identity { display: flex; flex-direction: column; align-items: center; }
  .person-name {
    font-family: "Caveat", "Comic Sans MS", cursive;
    font-weight: 700;
    font-size: 36px;
    line-height: 1;
    color: var(--ink-green);
  }
  .person-role { font-style: italic; font-size: 13px; color: var(--ink-green); margin-top: 2px; }
  .contact { list-style: none; font-size: 12px; color: var(--ink-dark); }
  .contact li { display: flex; align-items: center; justify-content: center; gap: 6px; margin-bottom: 3px; }
  .contact svg { width: 12px; height: 12px; fill: var(--ink-dark); flex: none; }
  .credentials { list-style: none; font-size: 13px; line-height: 1.45; color: var(--ink-dark); }
</style>
</head>
<body>
  <section class="card card-front">
    <div class="brand">
      <div class="brand-mark"></div>
      <h1 class="brand-name">Bright<br>Otter<br>Tutoring</h1>
    </div>
    <p class="front-email">BrightOtterTutoring@quillmail.example</p>
  </section>

  <section class="card card-back">
    <div class="identity">
      <h2 class="person-name">Mara Tolliver</h2>
      <p class="person-role">Tutor</p>
    </div>
    <ul class="contact">
      <li>
        <svg viewBox="0 0 24 24" aria-hidden="true"><path d="M6.6 10.8a15.1 15.1 0 0 0 6.6 6.6l2.2-2.2a1 1 0 0 1 1-.25 11.4 11.4 0 0 0 3.6.57 1 1 0 0 1 1 1V20a1 1 0 0 1-1 1A17 17 0 0 1 3 4a1 1 0 0 1 1-1h3.5a1 1 0 0 1 1 1c0 1.25.2 2.45.57 3.6a1 1 0 0 1-.25 1z"/></svg>
        <span>555.010.482</span>
      </li>
      <li>
        <svg viewBox="0 0 24 24" aria-hidden="true"><path d="M2 5h20v14H2z M4 7v.4l8 5.2 8-5.2V7z" fill-rule="evenodd"/></svg>
        <span>BrightOtterTutoring@quillmail.example</span>
      </li>
    </ul>
    <ul class="credentials">
      <li>Private Academic Tutor, Grades K-8</li>
      <li>Licensed Harwick Unified Schools Teacher</li>
      <li>Delmont Ridge University, M.S. Education</li>
      <li>Carrow Bay University, B.S. Journalism</li>
    </ul>
  </section>
</body>
</html>
```